Business Card Design

Electronic Security
Alarm Systems
CCTV
Electronic Access Control
Security System Integration

Industry/Entity Type

Business

Contact Information for Business Card

Gareth Linwood
PO Box 862
Ashgrove Qld 4071
Phone 07 38526147
Mob 0427395816

```html
<!DOCTYPE html>
<html lang="en">
<head>
<meta charset="utf-8">
<title>Gareth Linwood – Business Card</title>
<link rel="stylesheet" href="https://fonts.googleapis.com/css2?family=Arimo:wght@400;700&display=swap">
<style>
  :root {
    --backdrop: #e9e6e1;
    --card-white: #ffffff;
    --card-blue: #22a2df;
    --accent-yellow: #f5c80f;
    --ink: #111111;
    --brand-ink: #2a3b4c;
    --icon-bg: #111111;
  }
  html, body {
    margin: 0;
    padding: 0;
    width: 1200px;
    height: 800px;
    overflow: hidden;
    background: var(--backdrop);
  }
  .canvas {
    width: 1200px;
    height: 800px;
    display: flex;
    align-items: center;
    justify-content: center;
  }
  .business-card {
    width: 1000px;
    height: 570px;
    box-shadow: 0 14px 40px rgba(0,0,0,0.18);
    display: block;
  }
  .card-text { font-family: "Arimo", Arial, sans-serif; }
  .holder-name { font-size: 42px; font-weight: 700; fill: var(--ink); letter-spacing: 1px; }
  .brand-name { font-size: 74px; font-weight: 400; fill: var(--brand-ink); letter-spacing: 2px; }
  .contact-line { font-size: 24px; fill: var(--ink); }
  .service-line { font-size: 23px; fill: var(--ink); }
  .card-white { fill: var(--card-white); }
  .card-blue { fill: var(--card-blue); }
  .divider { stroke: var(--accent-yellow); stroke-width: 8; }
  .brand-square { fill: var(--card-blue); }
  .icon-box { fill: var(--icon-bg); }
  .icon-glyph { fill: var(--accent-yellow); }
</style>
</head>
<body>
<main class="canvas">
  <svg class="business-card" viewBox="0 0 1000 570" xmlns="http://www.w3.org/2000/svg" role="img" aria-label="Business card for Gareth Linwood, Korva electronic security">
    <rect class="card-white" x="0" y="0" width="1000" height="570"/>
    <polygon class="card-blue" points="0,540 1000,170 1000,570 0,570"/>
    <line class="divider" x1="0" y1="540" x2="1000" y2="170"/>

    <g class="brand-lockup card-text">
      <rect class="brand-square" x="60" y="170" width="62" height="62"/>
      <text class="brand-name" x="140" y="228">KORVA</text>
    </g>

    <text class="holder-name card-text" x="950" y="95" text-anchor="end">Gareth&#160;&#160;Linwood</text>

    <g class="contact-block card-text">
      <text class="contact-line" x="900" y="318" text-anchor="end">07 38526147</text>
      <text class="contact-line" x="900" y="362" text-anchor="end">0427395816</text>
      <text class="contact-line" x="900" y="406" text-anchor="end">PO Box 862 Ashgrove</text>
      <text class="contact-line" x="900" y="438" text-anchor="end">Qld 4071</text>
    </g>

    <g class="contact-icons">
      <g class="icon-phone" transform="translate(925,298)">
        <rect class="icon-box" width="30" height="24"/>
        <path class="icon-glyph" d="M7 9 q8 -6 16 0 v3 h-4 v-2 h-8 v2 h-4z M9 13 h12 l2 6 h-16z"/>
      </g>
      <g class="icon-mobile" transform="translate(925,342)">
        <rect class="icon-box" width="30" height="24"/>
        <rect class="icon-glyph" x="11" y="4" width="8" height="16" rx="1.5"/>
        <rect class="icon-box" x="12.5" y="6" width="5" height="6"/>
      </g>
      <g class="icon-home" transform="translate(925,396)">
        <rect class="icon-box" width="30" height="24"/>
        <path class="icon-glyph" d="M15 4 l9 8 h-3 v8 h-4 v-5 h-4 v5 h-4 v-8 h-3z"/>
      </g>
    </g>

    <g class="services card-text">
      <text class="service-line" x="960" y="500" text-anchor="end">Electronic Security , Alarm Systems , Electronic Access Control</text>
      <text class="service-line" x="800" y="534" text-anchor="end">CCTV , Security System Integration</text>
    </g>
  </svg>
</main>
</body>
</html>
```